Stationary Set Rebrand for Brennick

We are a Canadian Distribution and Service Company that was established in 1969. Over the past 5 decades we have expanded our business and have warehouses across Canada. We specialize in adhesive tapes, adhesives, films, safety, warehouse, shipping, janitorial and packaging supplies.

We have updated our logo design and would like a new corporate branding identity that includes a new fresh Stationary Set (Business Cards, Letterhead, Letterhead MS Word, Envelope, Presentation Folders, Email Signatures, Notepad Covers, etc.)

Target Market(s)

Industrial Business Sector

Font styles to use
Sans Serif

Colors
0054AA
0677BA
7BADD7
CADEEF
E8F1F8
0094D4
00A9DD
6FCCEA
C7EBF8
E9F6FB
00AB8E
00BBA5
67D7C9
C6EFE9
E9F9F6
EB3D1F
EC4F4E
F09395
F8D3D4
FCEDEE

Requirements
Should not have
• Colors not too light, darker colours preferred

```html
<!DOCTYPE html>
<html lang="en">
<head>
<meta charset="utf-8">
<title>Brennick Business Card</title>
<link rel="stylesheet" href="https://fonts.googleapis.com/css2?family=Exo+2:wght@400;500;800&family=Michroma&display=swap">
<style>
  :root {
    --page-bg: #e4e4e4;
    --card-white: #ffffff;
    --brand-red: #d71920;
    --ink-black: #231f20;
    --text-white: #ffffff;
  }
  * { box-sizing: border-box; margin: 0; padding: 0; }
  html, body {
    width: 1200px;
    height: 1200px;
    overflow: hidden;
    background: var(--page-bg);
  }
  .canvas {
    position: relative;
    width: 1200px;
    height: 1200px;
    font-family: "Exo 2", Arial, sans-serif;
  }
  .card {
    position: absolute;
    left: 252px;
    width: 696px;
    height: 398px;
    overflow: hidden;
  }
  .card-front { top: 156px; background: var(--brand-red); }
  .card-back  { top: 650px; background: var(--brand-red); }

  .front-header {
    position: absolute;
    left: 0; top: 0;
    width: 100%;
    height: 215px;
    background: var(--card-white);
    display: flex;
    align-items: center;
    justify-content: center;
  }
  .header-rule {
    position: absolute;
    left: 0; top: 215px;
    width: 100%;
    height: 6px;
    background: var(--ink-black);
  }
  .brand-name {
    font-family: "Exo 2", Arial, sans-serif;
    font-weight: 800;
    font-size: 76px;
    letter-spacing: 1px;
    color: var(--ink-black);
    line-height: 1;
  }
  .brand-mark {
    width: 18px;
    height: 18px;
    background: var(--brand-red);
    margin-left: 14px;
    align-self: flex-end;
    margin-bottom: 62px;
  }

  .person {
    position: absolute;
    right: 339px;
    top: 262px;
    text-align: right;
    color: var(--text-white);
  }
  .person-name {
    font-family: "Michroma", Arial, sans-serif;
    font-size: 21px;
    font-weight: 400;
    letter-spacing: 0.5px;
    line-height: 1;
    margin-bottom: 6px;
    -webkit-text-stroke: 1px var(--text-white);
  }
  .person-line {
    font-size: 16.5px;
    line-height: 21px;
    letter-spacing: 0.6px;
  }
  .divider {
    position: absolute;
    left: 373px;
    top: 263px;
    width: 2px;
    height: 97px;
    background: var(--text-white);
  }
  .contact-list {
    position: absolute;
    left: 386px;
    top: 268px;
    list-style: none;
    color: var(--text-white);
  }
  .contact-item {
    display: flex;
    align-items: center;
    height: 21px;
    font-size: 16.5px;
    letter-spacing: 0.6px;
  }
  .contact-icon {
    width: 14px;
    height: 14px;
    margin-right: 16px;
    fill: var(--text-white);
    flex: none;
  }

  .back-brand {
    position: absolute;
    inset: 0;
    display: flex;
    align-items: center;
    justify-content: center;
    font-weight: 800;
    font-size: 64px;
    letter-spacing: 1px;
    color: var(--text-white);
  }
</style>
</head>
<body>
<main class="canvas">
  <section class="card card-front">
    <header class="front-header">
      <span class="brand-name">Brennick</span>
      <span class="brand-mark"></span>
    </header>
    <div class="header-rule"></div>

    <div class="person">
      <p class="person-name">DANIEL MARSH</p>
      <p class="person-line">President</p>
      <p class="person-line">4120 Cedar Ridge Road</p>
      <p class="person-line">Halifax, Canada 20418</p>
    </div>

    <div class="divider"></div>

    <ul class="contact-list">
      <li class="contact-item">
        <svg class="contact-icon" viewBox="0 0 24 24" aria-hidden="true"><path d="M6.6 10.8a15.1 15.1 0 0 0 6.6 6.6l2.2-2.2c.3-.3.7-.4 1-.2 1.1.4 2.3.6 3.6.6.6 0 1 .4 1 1V20c0 .6-.4 1-1 1A17 17 0 0 1 3 4c0-.6.4-1 1-1h3.5c.6 0 1 .4 1 1 0 1.3.2 2.5.6 3.6.1.3 0 .7-.2 1z"/></svg>
        <span>555-214-8830</span>
      </li>
      <li class="contact-item">
        <svg class="contact-icon" viewBox="0 0 24 24" aria-hidden="true"><path d="M7 1h10a2 2 0 0 1 2 2v18a2 2 0 0 1-2 2H7a2 2 0 0 1-2-2V3a2 2 0 0 1 2-2zm0 3v14h10V4zm5 15.5a1.2 1.2 0 1 0 0 2.4 1.2 1.2 0 0 0 0-2.4z"/></svg>
        <span>555-390-4172</span>
      </li>
      <li class="contact-item">
        <svg class="contact-icon" viewBox="0 0 24 24" aria-hidden="true"><path d="M2 5h20v14H2zm2 2v.4l8 5.2 8-5.2V7zm0 2.8V17h16V9.8l-8 5.2z"/></svg>
        <span>info@brennick.com</span>
      </li>
      <li class="contact-item">
        <svg class="contact-icon" viewBox="0 0 24 24" aria-hidden="true"><path d="M12 2a10 10 0 1 0 0 20 10 10 0 0 0 0-20zm-1 17.9A8 8 0 0 1 4.2 10.2L9 15v1a2 2 0 0 0 2 2zm6.9-2.5A2 2 0 0 0 16 16h-1v-3a1 1 0 0 0-1-1H8v-2h2a1 1 0 0 0 1-1V7h2a2 2 0 0 0 2-2v-.4a8 8 0 0 1 2.9 12.8z"/></svg>
        <span>www.brennick.com</span>
      </li>
    </ul>
  </section>

  <section class="card card-back">
    <span class="back-brand">Brennick</span>
  </section>
</main>
</body>
</html>
```